Voltaryn - Web Design Project

I am looking for a 5 page design.
I would like it to be like the design of this site: www.quorvexlabs.com.
Which means it can be all one page effectively. With quick scroll tabs at the top.
I would like it to include parallax scrolling (The parallax effect uses multiple backgrounds which seem to move at different speeds to create a sensation of depth (creating a faux-3D effect)).
I have uploaded my logo. I would like this to be used in the site design.
I would like the site design to include 3D DNA creative.
Please note the Pixmora photos attached do not belong to me they are purely to inspire creative ideas. However I would be more than happy to purchase these photos to use if the designer thought this would be beneficial.
Requirements
Must have
- parallax scrolling
DNA pictures (3D effect)
Please use site for reference: www.quorvexlabs.com
Use at least 1 of the logos in design...

```html
<!DOCTYPE html>
<html lang="en">
<head>
<meta charset="utf-8">
<title>Voltaryn</title>
<link href="https://fonts.googleapis.com/css2?family=Ubuntu:wght@400;500;700&display=swap" rel="stylesheet">
<style>
:root{
  --red:#a5161c;
  --red-dark:#8c0f14;
  --ink:#3b3b3b;
  --muted:#6d6d6d;
  --header-bg:#f4f4f4;
  --section-alt:#f2f2f3;
  --pink:#f3c3c8;
  --footer-bg:#efefef;
  --btn:#3a3a3a;
}
*{margin:0;padding:0;box-sizing:border-box}
html,body{width:736px;height:1200px;overflow:hidden}
body{position:relative;font-family:"Ubuntu",sans-serif;color:var(--ink);background:#fff}
.abs{position:absolute}
.site-header{left:0;top:0;width:736px;height:95px;background:linear-gradient(#fafafa,var(--header-bg))}
.brand{left:80px;top:52px;display:flex;align-items:center;gap:6px;font-size:15px;font-weight:500;letter-spacing:2px;color:var(--red)}
.brand-dot{width:10px;height:10px;background:var(--red);border-radius:50%}
.main-nav{left:270px;top:64px;display:flex;align-items:center;font-size:8.5px;font-weight:500;color:#222}
.main-nav a{color:inherit;text-decoration:none;padding:0 11px}
.main-nav .sep{color:#444}
.main-nav .active{background:var(--red);color:#fff;height:18px;line-height:18px;padding:0 12px;margin-right:4px}
.hero{left:0;top:95px;width:736px;height:278px;background:linear-gradient(110deg,#8fcbe9,#3ea2d8 45%,#7cc4ea 75%,#2b8fcb)}
.hero-dots{left:609px;top:356px;display:flex;gap:3px}
.hero-dots span{width:9px;height:9px;border-radius:50%;background:#555}
.intro{left:0;top:373px;width:736px;height:209px;background:#fff}
.about-do{left:0;top:582px;width:736px;height:250px;background:linear-gradient(170deg,#fafafa,var(--section-alt))}
.frame{border:1px solid #ddd;padding:3px;background:#fff;box-shadow:0 1px 2px rgba(0,0,0,.08)}
.frame div{width:100%;height:100%}
.block-title{font-size:17px;font-weight:400;color:var(--red)}
.block-text{font-size:7.3px;line-height:14.1px;color:var(--muted);width:330px}
.btn{background:var(--btn);color:#fff;font-size:7.5px;height:20px;width:55px;line-height:20px;text-align:center;border-radius:2px}
.services{left:0;top:832px;width:736px;height:281px;background:linear-gradient(160deg,#f6d0d4,var(--pink))}
.services-title{left:80px;top:854px;font-size:16.5px;color:var(--red)}
.card{width:185px}
.card .frame{height:99px}
.card h3{margin-top:10px;font-size:10.5px;font-weight:500;color:#333}
.card p{margin-top:3px;font-size:7.2px;line-height:14.1px;color:#555}
.card .more{margin-top:12px;font-size:7.3px;font-weight:500;color:#333}
.arrow{top:960px}
.site-footer{left:0;top:1113px;width:736px;height:87px;background:var(--footer-bg)}
.footer-nav{left:80px;top:1137px;font-size:7.5px;color:var(--red)}
.footer-nav span{color:#777;margin:0 3px}
.copyright{left:80px;top:1173px;font-size:6.5px;color:#555}
.copyright b{font-weight:400;color:var(--red)}
.update{left:560px;top:1135px;font-size:8.5px;font-weight:500;color:var(--red)}
.social{left:561px;top:1153px;display:flex;gap:6px}
.social span{width:20px;height:20px;border-radius:3px}
</style>
</head>
<body>
<header class="abs site-header">
  <div class="abs brand"><span class="brand-dot"></span>VOLTARYN</div>
  <nav class="abs main-nav">
    <a class="active">HOME</a>
    <a>ABOUT US</a><span class="sep">|</span>
    <a>SERVICES</a><span class="sep">|</span>
    <a>RESEARCH</a><span class="sep">|</span>
    <a>BLOG</a><span class="sep">|</span>
    <a>CONTACT</a>
  </nav>
</header>

<section class="abs hero" role="img" aria-label="Colourful 3D DNA double helix over a blue molecular background"></section>
<div class="abs hero-dots"><span></span><span></span><span></span><span></span></div>

<section class="abs intro"></section>
<div class="abs frame" style="left:80px;top:397px;width:184px;height:142px"><div role="img" aria-label="Blue DNA strand on white" style="background:linear-gradient(135deg,#e7f4fc,#6bc0ee 55%,#d8eefb)"></div></div>
<h2 class="abs block-title" style="left:325px;top:394px">Who We Are</h2>
<p class="abs block-text" style="left:325px;top:421px">Aliquam molestie, mi et imperdiet euismod, dui purus auctor tellus, et interdum lacus lectus et ante. Sed accumsan sollicitudin sapien, sit amet adipiscing turpis gravida ac. In congue, neque ac lobortis volutpat, libero mauris varius mi, vitae suscipit ipsum ligula vitae risus. Duis aliquam nibh a dui iaculis viverra id a velit. Vivamus egestas risus in magna varius commodo. Sed semper viverra egestas.Aenean a nibh eget turpis vehicula tempus ac sed massa. Vestibulum dolor nulla, ultrices ac tincidunt sed, laoreet non est.</p>
<div class="abs btn" style="left:325px;top:541px">READ MORE</div>

<section class="abs about-do"></section>
<div class="abs frame" style="left:80px;top:613px;width:184px;height:141px"><div role="img" aria-label="Scientists working in a laboratory" style="background:linear-gradient(120deg,#b9cfdf,#e8eef2 50%,#c9d3db)"></div></div>
<h2 class="abs block-title" style="left:325px;top:609px">What We Do</h2>
<p class="abs block-text" style="left:325px;top:636px">Aliquam molestie, mi et imperdiet euismod, dui purus auctor tellus, et interdum lacus lectus et ante. Sed accumsan sollicitudin sapien, sit amet adipiscing turpis gravida ac. In congue, neque ac lobortis volutpat, libero mauris varius mi, vitae suscipit ipsum ligula vitae risus. Duis aliquam nibh a dui iaculis viverra id a velit. Vivamus egestas risus in magna varius commodo. Sed semper viverra egestas.Aenean a nibh eget turpis vehicula tempus ac sed massa. Vestibulum dolor nulla, ultrices ac tincidunt sed, laoreet non est. Nunc dignissim lectus vitae eros placerat euismod. Aenean lacinia sodales eros, sit amet molestie enim consectetur eget. Sed vel magna vel eros adipiscing adipiscing eu sit amet turpis. Mauris et massa sed lacus tempus pellentesque.</p>
<div class="abs btn" style="left:325px;top:793px">READ MORE</div>

<section class="abs services"></section>
<h2 class="abs services-title">Service We Offers</h2>
<svg class="abs arrow" style="left:50px" width="20" height="28" viewBox="0 0 20 28"><path d="M15 3 5 14l10 11" fill="none" stroke="#fff" stroke-width="4"/></svg>
<svg class="abs arrow" style="left:667px" width="20" height="28" viewBox="0 0 20 28"><path d="M5 3l10 11L5 25" fill="none" stroke="#fff" stroke-width="4"/></svg>

<div class="abs card" style="left:80px;top:889px">
  <div class="frame"><div role="img" aria-label="Red and blue DNA model" style="background:linear-gradient(135deg,#f4f4f6,#d9606a 40%,#5a86d6 70%,#eee)"></div></div>
  <h3>Morbi iaculis fringilla gravida</h3>
  <p>Vestibulum vel metus sit amet turpis bibendum tincidunt vel sit amet quam. Pellentesque habitant morbi tristique senectus et netus et malesuada fames ac turpis egestas.</p>
  <div class="more">READ MORE &gt;&gt;</div>
</div>
<div class="abs card" style="left:276px;top:889px">
  <div class="frame"><div role="img" aria-label="Researcher handling lab samples" style="background:linear-gradient(120deg,#c8d6e4,#f2f2f2 55%,#d8d2c8)"></div></div>
  <h3>Morbi iaculis fringilla gravida</h3>
  <p>Vestibulum vel metus sit amet turpis bibendum tincidunt vel sit amet quam. Pellentesque habitant morbi tristique senectus et netus et malesuada fames ac turpis egestas.</p>
  <div class="more">READ MORE &gt;&gt;</div>
</div>
<div class="abs card" style="left:472px;top:889px">
  <div class="frame"><div role="img" aria-label="Two scientists at a lab bench" style="background:linear-gradient(120deg,#9ab7d4,#e9eef3 50%,#6f8fb0)"></div></div>
  <h3>Morbi iaculis fringilla gravida</h3>
  <p>Vestibulum vel metus sit amet turpis bibendum tincidunt vel sit amet quam. Pellentesque habitant morbi tristique senectus et netus et malesuada fames ac turpis egestas.</p>
  <div class="more">READ MORE &gt;&gt;</div>
</div>

<footer class="abs site-footer"></footer>
<div class="abs footer-nav">Home<span>|</span>About Us<span>|</span>Services<span>|</span>Research<span>|</span>Blog<span>|</span>Contact</div>
<div class="abs copyright">Copyright © 2013 <b>Voltaryn</b>. All Right Reserved</div>
<div class="abs update">Update with us</div>
<div class="abs social">
  <span style="background:#3b5a9a" aria-label="Social link"></span>
  <span style="background:#4fb6e3" aria-label="Social link"></span>
  <span style="background:#1d78b4" aria-label="Social link"></span>
  <span style="background:#f08a24" aria-label="Feed link"></span>
</div>
</body>
</html>
```